Car wash line needed for the pylon inscription

We need a design template / print template for our advertising pylon so that the Korvane plates can be printed. The area to be printed is approx. 1.5m wide and approx. 2.70m high. We operate a car wash about 30m long. The washing rollers are equipped with scratch-free Velmo Tex foam material. Before the vehicle is put into the car wash it gets a manual high pressure pre-wash. There are four different washing programs: basic laundry € 7.50 (wheel cleaning, intensive washing, gloss drying comfort care € 10.50 (like base + active foam) special care € 13.00 (like comfort + glossy sealing with lotus wax) premium care € 15.50 (like special care + Underbody wash) The pylon is right on the driveway on a busy road, we want to achieve maximum attention with the pylons. It should not be too much content because the vehicles drive past it, due to an immediate gyro, the speed is however at about 40Km / h. Opening hours Mon-Fri. 08: 00-19: 00 Sat 07: 00-19: 00 The Korvane plates are red. The enclosed files show our pylon with a little appealing design proposal our advertising agency and the real local places. For the opinion you can see on the following link a youtube video with a comparable car wash like ours, the washing process is well illustrated there. https://www.clipvault-demo.net/watch?v=Qk7rTzP2mLw Furthermore, we have a bonus card system who has washed our car 10 times gets the 11 laundry for free. From foam additives we use active foam from the comfort care and from the special care gets the vehicle lotus wax, which has the effect that the paint is sealed and keeps the shine longer. We need a design template / print template for our advertising pylon so that the Korvane plates can be printed. The area to be printed is approx. 1.5m wide and approx. 2.70m high. We operate a car wash about 30m long. The washing rollers are equipped with scratch-free Velmo Tex foam material. Before the vehicle is put into the car wash it gets a manual high pressure pre-wash. There are four different washing programs: basic laundry € 7.50 (wheel cleaning, intensive washing, gloss drying comfort care € 10.50 (like base + active foam) special care € 13.00 (like comfort + glossy sealing with lotus wax) premium care € 15.50 (like special care + Underbody wash) The pylon is right on the driveway on a busy road, we want to achieve maximum attention with the pylons. It should not be too much content because the vehicles drive past it, due to an immediate gyro, the speed is however at about 40Km / h. Opening hours Mon-Fri. 08: 00-19: 00 Sat 07: 00-19: 00 The Korvane plates are red. The enclosed files show our pylon with a little appealing design proposal our advertising agency and the real local places. For the opinion you can see on the following link a youtube video with a comparable car wash like ours, the washing process is well illustrated there. https://www.clipvault-demo.net/watch?v=Qk7rTzP2mLw Furthermore, we have a bonus card system who has washed our car 10 times gets the 11 laundry for free. From foam additives we use active foam from the comfort care and from the special care gets the vehicle lotus wax, which has the effect that the paint is sealed and keeps the shine longer. We need a design template / print template for our advertising pylon so that the Korvane plates can be printed. The area to be printed is approx. 1.5m wide and approx. 2.70m high. We operate a car wash about 30m long. The washing rollers are equipped with scratch-free Velmo Tex foam material. Before the vehicle is put into the car wash it gets a manual high pressure pre-wash. There are four different washing programs: basic laundry € 7.50 (wheel cleaning, intensive washing, gloss drying comfort care € 10.50 (like base + active foam) special care € 13.00 (like comfort + glossy sealing with lotus wax) premium care € 15.50 (like special care + Underbody wash) The pylon is right on the driveway on a busy road, we want to achieve maximum attention with the pylons. It should not be too much content because the vehicles drive past it, due to an immediate gyro, the speed is however at about 40Km / h. Opening hours Mon-Fri. 08: 00-19: 00 Sat 07: 00-19: 00 The Korvane plates are red. The enclosed files show our pylon with a little appealing design proposal our advertising agency and the real local places. For the opinion you can see on the following link a youtube video with a comparable car wash like ours, the washing process is well illustrated there. https://www.clipvault-demo.net/watch?v=Qk7rTzP2mLw Furthermore, we have a bonus card system who has washed our car 10 times gets the 11 laundry for free. From foam additives we use active foam from the comfort care and from the special care gets the vehicle lotus wax, which has the effect that the paint is sealed and keeps the shine longer. We need a design template / print template for our advertising pylon so that the Korvane plates can be printed. The area to be printed is approx. 1.5m wide and approx. 2.70m high. We operate a car wash about 30m long. The washing rollers are equipped with scratch-free Velmo Tex foam material. Before the vehicle is put into the car wash it gets a manual high pressure pre-wash. There are four different washing programs: basic laundry € 7.50 (wheel cleaning, intensive washing, gloss drying comfort care € 10.50 (like base + active foam) special care € 13.00 (like comfort + glossy sealing with lotus wax) premium care € 15.50 (like special care + Underbody wash) The pylon is right on the driveway on a busy road, we want to achieve maximum attention with the pylons. It should not be too much content because the vehicles drive past it, due to an immediate gyro, the speed is however at about 40Km / h. Opening hours Mon-Fri. 08: 00-19: 00 Sat 07: 00-19: 00 The Korvane plates are red. The enclosed files show our pylon with a little appealing design proposal our advertising agency and the real local places. For the opinion you can see on the following link a youtube video with a comparable car wash like ours, the washing process is well illustrated there. https://www.clipvault-demo.net/watch?v=Qk7rTzP2mLw Furthermore, we have a bonus card system who has washed our car 10 times gets the 11 laundry for free. From foam additives we use active foam from the comfort care and from the special care gets the vehicle lotus wax, which has the effect that the paint is sealed and keeps the shine longer. We need a design template / print template for our advertising pylon so that the Korvane plates can be printed. The area to be printed is approx. 1.5m wide and approx. 2.70m high. We operate a car wash about 30m long. The washing rollers are equipped with scratch-free Velmo Tex foam material. Before the vehicle is put into the car wash it gets a manual high pressure pre-wash. There are four different washing programs: basic laundry € 7.50 (wheel cleaning, intensive washing, gloss drying comfort care € 10.50 (like base + active foam) special care € 13.00 (like comfort + glossy sealing with lotus wax) premium care € 15.50 (like special care + Underbody wash) The pylon is right on the driveway on a busy road, we want to achieve maximum attention with the pylons. It should not be too much content because the vehicles drive past it, due to an immediate gyro, the speed is however at about 40Km / h. Opening hours Mon-Fri. 08: 00-19: 00 Sat 07: 00-19: 00 The Korvane plates are red. The enclosed files show our pylon with a little appealing design proposal our advertising agency and the real local places. For the opinion you can see on the following link a youtube video with a comparable car wash like ours, the washing process is well illustrated there. https://www.clipvault-demo.net/watch?v=Qk7rTzP2mLw Furthermore, we have a bonus card system who has washed our car 10 times gets the 11 laundry for free. From foam additives we use active foam from the comfort care and from the special care gets the vehicle lotus wax, which has the effect that the paint is sealed and keeps the shine longer. We need a design template / print template for our advertising pylon so that the Korvane plates can be printed. The area to be printed is approx. 1.5m wide and approx. 2.70m high. We operate a car wash about 30m long. The washing rollers are equipped with scratch-free Velmo Tex foam material. Before the vehicle is put into the car wash it gets a manual high pressure pre-wash. There are four different washing programs: basic laundry € 7.50 (wheel cleaning, intensive washing, gloss drying comfort care € 10.50 (like base + active foam) special care € 13.00 (like comfort + glossy sealing with lotus wax) premium care € 15.50 (like special care + Underbody wash) The pylon is right on the driveway on a busy road, we want to achieve maximum attention with the pylons. It should not be too much content because the vehicles drive past it, due to an immediate gyro, the speed is however at about 40Km / h. Opening hours Mon-Fri. 08: 00-19: 00 Sat 07: 00-19: 00 The Korvane plates are red. The enclosed files show our pylon with a little appealing design proposal our advertising agency and the real local places. For the opinion you can see on the following link a youtube video with a comparable car wash like ours, the washing process is well illustrated there. https://www.clipvault-demo.net/watch?v=Qk7rTzP2mLw Furthermore, we have a bonus card system who has washed our car 10 times gets the 11 laundry for free. From foam additives we use active foam from the comfort care and from the special care gets the vehicle lotus wax, which has the effect that the paint is sealed and keeps the shine longer. We need a design template / print template for our advertising pylon so that the Korvane plates can be printed. The area to be printed is approx. 1.5m wide and approx. 2.70m high. We operate a car wash about 30m long. The washing rollers are equipped with scratch-free Velmo Tex foam material. Before the vehicle is put into the car wash it gets a manual high pressure pre-wash. There are four different washing programs: basic laundry € 7.50 (wheel cleaning, intensive washing, gloss drying comfort care € 10.50 (like base + active foam) special care € 13.00 (like comfort + glossy sealing with lotus wax) premium care € 15.50 (like special care + Underbody wash) The pylon is right on the driveway on a busy road, we want to achieve maximum attention with the pylons. It should not be too much content because the vehicles drive past it, due to an immediate gyro, the speed is however at about 40Km / h. Opening hours Mon-Fri. 08: 00-19: 00 Sat 07: 00-19: 00 The Korvane plates are red. The enclosed files show our pylon with a little appealing design proposal our advertising agency and the real local places. For the opinion you can see on the following link a youtube video with a comparable car wash like ours, the washing process is well illustrated there. https://www.clipvault-demo.net/watch?v=Qk7rTzP2mLw Furthermore, we have a bonus card system who has washed our car 10 times gets the 11 laundry for free. From foam additives we use active foam from the comfort care and from the special care gets the vehicle lotus wax, which has the effect that the paint is sealed and keeps the shine longer. We need a design template / print template for our advertising pylon so that the Korvane plates can be printed. The area to be printed is approx. 1.5m wide and approx. 2.70m high. We operate a car wash about 30m long. The washing rollers are equipped with scratch-free Velmo Tex foam material. Before the vehicle is put into the car wash it gets a manual high pressure pre-wash. There are four different washing programs: basic laundry € 7.50 (wheel cleaning, intensive washing, gloss drying comfort care € 10.50 (like base + active foam) special care € 13.00 (like comfort + glossy sealing with lotus wax) premium care € 15.50 (like special care + Underbody wash) The pylon is right on the driveway on a busy road, we want to achieve maximum attention with the pylons. It should not be too much content because the vehicles drive past it, due to an immediate gyro, the speed is however at about 40Km / h. Opening hours Mon-Fri. 08: 00-19: 00 Sat 07: 00-19: 00 The Korvane plates are red. The enclosed files show our pylon with a little appealing design proposal our advertising agency and the real local places. For the opinion you can see on the following link a youtube video with a comparable car wash like ours, the washing process is well illustrated there. https://www.clipvault-demo.net/watch?v=Qk7rTzP2mLw Furthermore, we have a bonus card system who has washed our car 10 times gets the 11 laundry for free. From foam additives we use active foam from the comfort care and from the special care gets the vehicle lotus wax, which has the effect that the paint is sealed and keeps the shine longer. We need a design template / print template for our advertising pylon so that the Korvane plates can be printed. The area to be printed is approx. 1.5m wide and approx. 2.70m high. We operate a car wash about 30m long. The washing rollers are equipped with scratch-free Velmo Tex foam material. Before the vehicle is put into the car wash it gets a manual high pressure pre-wash. There are four different washing programs: basic laundry € 7.50 (wheel cleaning, intensive washing, gloss drying comfort care € 10.50 (like base + active foam) special care € 13.00 (like comfort + glossy sealing with lotus wax) premium care € 15.50 (like special care + Underbody wash) The pylon is right on the driveway on a busy road, we want to achieve maximum attention with the pylons. It should not be too much content because the vehicles drive past it, due to an immediate gyro, the speed is however at about 40Km / h. Opening hours Mon-Fri. 08: 00-19: 00 Sat 07: 00-19: 00 The Korvane plates are red. The enclosed files show our pylon with a little appealing design proposal our advertising agency and the real local places. For the opinion you can see on the following link a youtube video with a comparable car wash like ours, the washing process is well illustrated there. https://www.clipvault-demo.net/watch?v=Qk7rTzP2mLw Furthermore, we have a bonus card system who has washed our car 10 times gets the 11 laundry for free. From foam additives we use active foam from the comfort care and from the special care gets the vehicle lotus wax, which has the effect that the paint is sealed and keeps the shine longer.

Target Market(s)

germany

Colors

Designer to choose colors to be used in the design.

Requirements
Must have
• Print template for the print job in the accepted formats. Of course, the design must be in German
Nice to have
• Colors that attract attention, but are still serious. The content must be perceived when passing by and the customers must be aware of the car wash.
Should not have
• Kitschiges Design Too much content which takes longer to be read.

```html
<!DOCTYPE html>
<html lang="de">
<head>
<meta charset="utf-8">
<title>Autowäsche – Pylon</title>
<link rel="stylesheet" href="https://fonts.googleapis.com/css2?family=Anton&family=Montserrat:ital,wght@0,700;0,800;0,900;1,700;1,800;1,900&family=Oswald:wght@600;700&display=swap">
<style>
  :root {
    --pylon-frame: #000000;
    --navy: #011c3a;
    --sky: #00b4f0;
    --sky-light: #d8f6ff;
    --ribbon: #0db2f2;
    --ribbon-fold: #0b4c9a;
    --signal-red: #ed1c24;
    --signal-yellow: #ffe100;
    --seal-blue: #1a8fe0;
    --white: #ffffff;
    --silver: #b9bfc7;
  }
  html, body {
    margin: 0;
    padding: 0;
    width: 960px;
    height: 1200px;
    overflow: hidden;
    background: var(--white);
  }
  .pylon { display: block; width: 960px; height: 1200px; }
  .headline { font-family: "Anton", "Oswald", sans-serif; fill: var(--signal-red); }
  .wide { font-family: "Montserrat", sans-serif; font-weight: 900; }
  .condensed { font-family: "Oswald", "Arial Narrow", sans-serif; font-weight: 700; }
  .ital { font-family: "Montserrat", sans-serif; font-style: italic; font-weight: 800; }
  .label { font-family: "Montserrat", sans-serif; font-weight: 700; }
  .t-white { fill: var(--white); }
  .t-yellow { fill: var(--signal-yellow); }
  .ribbon { fill: var(--ribbon); }
  .ribbon-fold { fill: var(--ribbon-fold); }
</style>
</head>
<body>
<svg class="pylon" viewBox="0 0 960 1200" xmlns="http://www.w3.org/2000/svg">
  <defs>
    <radialGradient id="burst" cx="0.5" cy="0.45" r="0.7">
      <stop offset="0" stop-color="var(--sky-light)"/>
      <stop offset="0.45" stop-color="#7fdcfb"/>
      <stop offset="1" stop-color="var(--sky)"/>
    </radialGradient>
    <linearGradient id="chrome" x1="0" y1="0" x2="0" y2="1">
      <stop offset="0" stop-color="var(--white)"/>
      <stop offset="1" stop-color="var(--silver)"/>
    </linearGradient>
    <linearGradient id="iconZone" x1="0" y1="0" x2="1" y2="1">
      <stop offset="0" stop-color="#0a2a50"/>
      <stop offset="1" stop-color="var(--navy)"/>
    </linearGradient>
  </defs>

  <!-- pylon frame and panel -->
  <rect class="frame" x="182" y="98" width="594" height="1014" fill="var(--pylon-frame)"/>
  <rect class="panel" x="216" y="128" width="528" height="963" fill="var(--navy)"/>

  <!-- hero area -->
  <polygon class="hero" role="img" aria-label="Illustration: glänzendes blaues Auto frontal vor Lichtstrahlen mit Seifenblasen und Glanzsternen"
           points="216,335 744,221 744,542 216,661" fill="url(#burst)"/>
  <polygon class="hero-edge" points="216,661 744,542 744,553 216,672" fill="var(--signal-yellow)"/>

  <!-- headline -->
  <text class="headline" transform="translate(233,317) rotate(-11.6)" x="0" y="0"
        font-size="84" textLength="500" lengthAdjust="spacingAndGlyphs">AUTOWÄSCHE</text>

  <!-- offer block -->
  <g class="offer-line" transform="translate(238,716) rotate(-13.5)">
    <polygon class="ribbon-fold" points="0,0 16,0 16,13"/>
    <polygon class="ribbon" points="5,-34 324,-34 316,0 0,0"/>
    <text class="wide t-white" x="10" y="-8" font-size="24" textLength="295" lengthAdjust="spacingAndGlyphs">LACKSCHONEND MIT</text>
  </g>
  <text class="wide t-yellow" transform="translate(258,756) rotate(-13.5)" font-size="46" textLength="292" lengthAdjust="spacingAndGlyphs">VELMO TEX</text>
  <text class="wide t-white" transform="translate(258,781) rotate(-13.5)" font-size="25" textLength="348" lengthAdjust="spacingAndGlyphs">SCHAUMSTOFF - WALZEN</text>

  <g class="offer-line" transform="translate(238,834) rotate(-13.5)">
    <polygon class="ribbon-fold" points="0,0 16,0 16,13"/>
    <polygon class="ribbon" points="5,-36 200,-36 192,0 0,0"/>
    <text class="wide t-white" x="20" y="-8" font-size="29" textLength="160" lengthAdjust="spacingAndGlyphs">NUR HIER!</text>
  </g>
  <text class="wide t-white" transform="translate(259,857) rotate(-13.5)" font-size="21" textLength="82" lengthAdjust="spacingAndGlyphs">WASCH</text>
  <text class="wide t-yellow" transform="translate(261,884) rotate(-13.5)" font-size="38" textLength="217" lengthAdjust="spacingAndGlyphs">GUTSCHEINE!</text>
  <text class="condensed t-white" transform="translate(261,905) rotate(-13.5)" font-size="22" textLength="207" lengthAdjust="spacingAndGlyphs">Sparen Sie 10% für 10 x</text>

  <g class="offer-line" transform="translate(238,954) rotate(-13.5)">
    <polygon class="ribbon-fold" points="0,0 16,0 16,13"/>
    <polygon class="ribbon" points="5,-38 326,-38 318,0 0,0"/>
    <text class="wide t-white" x="24" y="-9" font-size="27" textLength="280" lengthAdjust="spacingAndGlyphs">PERFEKTE WÄSCHE</text>
  </g>
  <text class="wide t-yellow" transform="translate(261,984) rotate(-13.5)" font-size="35" textLength="332" lengthAdjust="spacingAndGlyphs">AUCH FÜR 1HR AUTO</text>

  <!-- launch seal -->
  <g class="seal">
    <circle cx="649" cy="781" r="74" fill="var(--signal-red)"/>
    <circle cx="649" cy="781" r="76" fill="none" stroke="var(--signal-red)" stroke-width="10"
            stroke-dasharray="5 7" stroke-linecap="round"/>
    <circle cx="649" cy="781" r="64" fill="var(--seal-blue)" stroke="var(--signal-yellow)" stroke-width="5"/>
    <g text-anchor="middle" class="t-white">
      <text class="condensed" x="650" y="757" font-size="22">Ab xx.xx.</text>
      <text class="condensed" x="649" y="776" font-size="20">TESTEN</text>
      <text class="label" x="652" y="790" font-size="12">und gratis</text>
      <text class="label" x="652" y="802" font-size="12">einen</text>
      <text class="label" x="652" y="814" font-size="12">Cappuccino</text>
      <text class="label" x="652" y="826" font-size="12">genießen</text>
    </g>
  </g>

  <!-- car line icon zone -->
  <rect class="car-icon" role="img" aria-label="Linienzeichnung eines Sportwagens mit Glanzsternen"
        x="604" y="884" width="128" height="82" rx="6" fill="url(#iconZone)"/>

  <!-- extras -->
  <text class="ital t-yellow" x="731" y="996" font-size="22" text-anchor="end" textLength="232" lengthAdjust="spacingAndGlyphs">ETWAS BESONDERES</text>
  <text class="ital" x="729" y="1024" font-size="31" font-weight="900" text-anchor="end"
        fill="url(#chrome)" textLength="362" lengthAdjust="spacingAndGlyphs">ZUSÄTZLICH LOTUSWACHS</text>

  <!-- opening hours -->
  <text class="label t-white" x="246" y="1044" font-size="15">ÖFFNUNGSZEITEN</text>
  <rect class="hours-bar" x="216" y="1050" width="528" height="27" fill="var(--signal-red)"/>
  <text class="ital t-white" x="243" y="1071" font-size="20" font-weight="700" textLength="478" lengthAdjust="spacingAndGlyphs">Mo-Frei. 08:00-19:00 Uhr,  Sa 07:00-19:00 Uhr</text>
</svg>
</body>
</html>
```